Design my site www.brieflyledger.com

So here is what I am thinking in terms of design:

https://plenvo.com

https://www.skyluxair.com

http://kalvex.com/harbor-plaza-tower/

I want the theme to be white and blue (royal blue). I attached a paint picture of what I would like the site to look like in terms of placing the text. Generally, what I like about the sites above is that they are simple, you can navigate easily and have some kind of idea of what's going on by looking at the center (picture and motto). Let's establish a clear understanding of how the functional part of the site would look like. Please see the picture attached.

I want to keep it simple: On top would be the Name 'BRIEFLY ledger", somewhere to the right on top on the page would be 'Sign in" button.

In the center would be a picture (maybe a video) with the Motto (on top of it all in capital) OBSERVE NAVIGATE DECIDE and below would be the "sign up now"

Below the picture (like on kalvex.com site) or to the left on top of the page would be "About Us', "Press" "Contact Us' buttons.

Then once the user gets to his page his got 3 tabs " Press Headlines", "Events", " Briefings".

we would keep the same format I only have on the site, but separate for every Tab.

I do not want the user to get distracted. I also want him to be able to access the page though mobile phone and be able to get automatic updates just like Zorvan Pings without having to sign in daily.

The landing page must be minimalist yet with business/corporate feel where users can navigate easily and a "what you see is what you get" approach. You want an image or video (personally I prefer the video.. it does capture the users attention instantly, as long as it is an interesting video), with your taglines in it.

Sections available to public: About Us, Contact Us, Landing Page with Signup Option

Private: Public Sections + User Account Page, Tabs for (Events, Press Headlines, Briefings)

Target Market(s)

PR/media monitoring/diplomatic community

Coding

Coded - Design and coding required

Number of Pages Required

1 page

Font styles to use
Serif
Sans Serif

Colors
0255a3
ec1f27

Requirements
Must have
• a simple landing page, that is user friendly.
Nice to have
• a video with the explanation of how to navigate the site
Should not have
• too many colors, graphs etc.

```html
<!DOCTYPE html>
<html lang="en">
<head>
<meta charset="utf-8">
<title>Briefly Ledger</title>
<link href="https://fonts.googleapis.com/css2?family=Roboto:wght@300;400;500&family=Roboto+Slab:wght@700&display=swap" rel="stylesheet">
<style>
:root{
  --royal:#0255a3;
  --red:#ec1f27;
  --red-dark:#c81d25;
  --ink:#555;
  --muted:#8f8f8f;
  --line:#e6e6e6;
  --tab-bg:#f2f2f2;
  --footer-bg:#f1f1f1;
}
*{margin:0;padding:0;box-sizing:border-box}
html,body{width:1200px;height:1022px;overflow:hidden;background:#fff;font-family:'Roboto',sans-serif}
.site-header{position:absolute;left:0;top:0;width:1200px;height:92px;border-bottom:1px solid #ddd;box-shadow:0 1px 3px rgba(0,0,0,.06);background:#fff}
.brand{position:absolute;left:98px;top:26px;display:flex;align-items:center;gap:12px}
.brand-mark{width:40px;height:40px;border-radius:50%;background:var(--red)}
.brand-name{font-family:'Roboto Slab',serif;font-weight:700;font-size:29px;color:var(--royal)}
.follow{position:absolute;left:726px;top:40px;display:flex;align-items:center;gap:20px;font-size:10px;color:#666;letter-spacing:.2px}
.follow .dot{width:11px;height:11px;border-radius:50%;background:var(--royal)}
.follow .dot.red{background:var(--red)}
.user{position:absolute;left:990px;top:26px;display:flex;align-items:center;gap:12px;font-size:12px;color:#999;font-weight:300}
.avatar{width:40px;height:40px;border-radius:50%;background:linear-gradient(#c9b8a8,#6c5a4c);border:2px solid #ddd}
.tabs{position:absolute;left:99px;top:133px;width:1002px;height:51px;border-bottom:1px solid var(--line)}
.tab{position:absolute;top:0;width:307px;height:51px;display:flex;align-items:center;justify-content:center;font-size:15px;color:var(--royal);background:var(--tab-bg);border:1px solid #e0e0e0;border-bottom:none}
.tab.active{background:var(--royal);color:#fff;border-color:var(--royal)}
.tab.active::after{content:"";position:absolute;left:50%;bottom:-7px;margin-left:-7px;border-left:7px solid transparent;border-right:7px solid transparent;border-top:7px solid var(--royal)}
.panel{position:absolute;left:99px;top:184px;width:1002px;height:230px;border-left:1px solid var(--line);border-right:1px solid var(--line);-webkit-mask-image:linear-gradient(#000,transparent);mask-image:linear-gradient(#000,transparent)}
.intro{position:absolute;left:124px;top:209px;width:945px;font-size:11px;line-height:23px;color:var(--ink);font-weight:400}
.article{position:absolute;left:123px;width:980px;height:280px}
.photo-frame{position:absolute;left:0;top:0;width:355px;height:280px;border:1px solid #e4e4e4;padding:6px;background:#fff}
.photo{width:100%;height:100%}
.article-body{position:absolute;left:402px;top:8px;width:532px}
.article-title{font-size:12.4px;line-height:22px;color:var(--royal);font-weight:400}
.article-text{margin-top:7px;font-size:10.8px;line-height:24px;color:var(--muted);font-weight:300}
.article-text+.article-text{margin-top:12px}
.date-btn{position:absolute;left:402px;top:234px;width:124px;height:37px;border-radius:19px;background:linear-gradient(var(--red),var(--red-dark));color:#fff;font-size:12px;font-weight:500;display:flex;align-items:center;justify-content:center}
.site-footer{position:absolute;left:0;top:931px;width:1200px;height:91px;background:var(--footer-bg)}
.copy{position:absolute;left:98px;top:39px;font-size:12px;color:#555}
.connect{position:absolute;left:818px;top:31px;display:flex;align-items:center;gap:6px;font-size:12px;color:#555}
.connect .ring{width:31px;height:31px;border-radius:50%;border:2px solid #bbb}
.connect .ring.on{border-color:var(--royal)}
.connect span{margin-right:3px}
</style>
</head>
<body>
<header class="site-header">
  <div class="brand"><div class="brand-mark"></div><div class="brand-name">Briefly Ledger</div></div>
  <div class="follow">FOLLOW US :<i class="dot red"></i><i class="dot"></i><i class="dot"></i><i class="dot"></i><i class="dot"></i></div>
  <div class="user">User Name<div class="avatar" role="img" aria-label="User profile photo"></div></div>
</header>

<nav class="tabs">
  <div class="tab active" style="left:0">Newspaper Headlines</div>
  <div class="tab" style="left:348px">Events</div>
  <div class="tab" style="left:695px">Daily Briefing</div>
</nav>
<div class="panel"></div>

<p class="intro">Lorem Ipsum is simply dummy text of the printing and typesetting industry. Lorem Ipsum has been the industry's standard dummy text ever since the 1500s, when an unknown printer took a galley of type and scrambled it to make a type specimen book. It has survived not only five centuries, but also the leap into electronic typesetting, remaining essentially unchanged.</p>

<article class="article" style="top:284px">
  <div class="photo-frame"><div class="photo" role="img" aria-label="Woman reading a newspaper at a cafe table" style="background:linear-gradient(135deg,#b9a58c,#8d6b4f 45%,#d8d2c6)"></div></div>
  <div class="article-body">
    <h3 class="article-title">Sed ut perspiciatis unde omnis iste natus error sit voluptatem accusantium doloremque lauda ntium, totam rem aperiam Nemo enim ipsam voluptatem</h3>
    <p class="article-text">Ipsum is simply dummy text of the printing and typesetting industry. Lorem Ipsum has been the istandard labore et dolore magnam aliquam quaerat voluptatem. Ut enim ad minima veniam, quis nostrum exercitati onem ullam corporis suscipit laboriosam, nisi ut aliquid ex ea commodi...</p>
    <p class="article-text">Dummy text ever since the 1500s, when an unknown printer took a numquam eius modi tempora incidunt ut labore et dolore magnam aliquam quaerat voluptatem. Ut enim ad minima veniam, quis nostrum exercitati onem ullam corporis suscipit laboriosam, nisi ut aliquid ex ea commodi...</p>
  </div>
  <div class="date-btn">23 June 2016</div>
</article>

<article class="article" style="top:601px">
  <div class="photo-frame"><div class="photo" role="img" aria-label="Two friends laughing while reading a newspaper together" style="background:linear-gradient(135deg,#c7a585,#a9785a 45%,#d9d6c9)"></div></div>
  <div class="article-body">
    <h3 class="article-title">Sed ut perspiciatis unde omnis iste natus error sit voluptatem accusantium doloremque lauda ntium, totam rem aperiam Nemo enim ipsam voluptatem</h3>
    <p class="article-text">Ipsum is simply dummy text of the printing and typesetting industry. Lorem Ipsum has been the istandard labore et dolore magnam aliquam quaerat voluptatem. Ut enim ad minima veniam, quis nostrum exercitati onem ullam corporis suscipit laboriosam, nisi ut aliquid ex ea commodi...</p>
    <p class="article-text">Dummy text ever since the 1500s, when an unknown printer took a numquam eius modi tempora incidunt ut labore et dolore magnam aliquam quaerat voluptatem. Ut enim ad minima veniam, quis nostrum exercitati onem ullam corporis suscipit laboriosam, nisi ut aliquid ex ea commodi...</p>
  </div>
  <div class="date-btn">23 June 2016</div>
</article>

<footer class="site-footer">
  <div class="copy">©brieflyledger.2016 |Allrights Reserved.</div>
  <div class="connect"><span>Connect With Us :</span><i class="ring on"></i><i class="ring"></i><i class="ring"></i><i class="ring"></i><i class="ring"></i></div>
</footer>
</body>
</html>
```